Brochure for a website accessibility report

This brochure is related to a report that www.qelvantrix.org sell. The report shows the results of an automated audit of a websites accessibility. It shows details of issues found with screen shots, examples of code and provides remediation advice.

The brochure will be a pdf 8.5 inches by 11 inches. It can be anywhere from 6 to 10 pages.

The FlintVue™ name itself should be “Bree Serif” font. The fonts, styles, colors and sizes are up to you.

The images used and logo of the Office of Digital Reachworks and K7P logo are upload

We highlighted in blue page extracts from the report we sell. Do not use the blue highlight, it is merely there to show you where the specific examples of the report we sell are vs the other content in the report. The areas in blue which show the content from the actual report should be shown as an extract of the actual page of the report. You have flexibility to change the layout and the way the content look.

The red square callouts over the blue content are callouts that describe the specific page extracts. We used it as a red callout only so that you would be able to see it. You should change the specific location, look and feel of the callout to be appropriate

Target Market(s)

Marketing and Technical people

Industry/Entity Type

Information Technology

Font styles to use
Sans Serif

Colors

Designer to choose colors to be used in the design.

Requirements
Should not have
• wheelchairs, images of blind people

```html
<!DOCTYPE html>
<html lang="en">
<head>
<meta charset="utf-8">
<title>FlintVue™ 2019 Brochure – Office of Digital Reachworks</title>
<link rel="stylesheet" href="https://fonts.googleapis.com/css2?family=Bree+Serif&family=Raleway:wght@400;500;700&display=swap">
<style>
  :root {
    --backdrop: #e2e2e2;
    --paper: #f1f1f1;
    --green: #23b062;
    --ink: #121417;
    --navy: #1d3a6e;
    --photo-top: #2b3a4e;
    --photo-mid: #3e5d7c;
    --photo-low: #1e2633;
    --white: #ffffff;
  }
  * { box-sizing: border-box; margin: 0; padding: 0; }
  html, body {
    width: 1200px; height: 840px; overflow: hidden;
    background: var(--backdrop);
  }
  .cover {
    position: absolute; left: 300px; top: 32px;
    width: 600px; height: 776px;
    background: var(--paper);
    overflow: hidden;
    box-shadow: 0 6px 20px rgba(0,0,0,.18);
    font-family: "Raleway", Arial, sans-serif;
  }

  /* Header band */
  .cover-header { position: absolute; left: 0; top: 0; width: 100%; height: 172px; }
  .org-name {
    position: absolute; left: 40px; top: 62px; width: 290px;
    font-family: "Raleway", Arial, sans-serif;
    font-weight: 700; font-size: 24px; line-height: 29px;
    color: var(--ink);
  }
  .org-mark {
    position: absolute; left: 350px; top: 60px;
    display: flex; flex-direction: column; align-items: center; gap: 6px;
  }
  .org-mark .disc { width: 58px; height: 58px; border-radius: 50%; background: var(--navy); }
  .org-mark .mark-name { font-size: 11px; font-weight: 700; color: var(--navy); }
  .mission-quote { position: absolute; left: 436px; top: 44px; width: 140px; }
  .mission-quote .quote-rule { display: block; height: 1px; background: var(--green); margin: 4px 0; }
  .mission-quote .quote-mark { color: var(--green); font-family: "Bree Serif", Georgia, serif; font-size: 22px; line-height: 18px; }
  .mission-quote p { font-size: 11px; line-height: 14px; color: var(--ink); margin: 4px 0; }
  .mission-quote .quote-url { font-size: 10px; font-weight: 500; text-align: right; color: var(--ink); }
  .mission-quote .quote-mark.close { text-align: right; }

  /* Photo area */
  .cover-photo {
    position: absolute; left: 0; top: 172px; width: 100%; height: 604px;
    background:
      radial-gradient(ellipse at 38% 30%, rgba(90,150,210,.55), transparent 55%),
      linear-gradient(180deg, var(--photo-top) 0%, var(--photo-mid) 55%, var(--photo-low) 100%);
  }
  .product-title {
    position: absolute; left: 0; top: 232px; width: 100%;
    text-align: center;
    font-family: "Bree Serif", Georgia, serif;
    font-size: 78px; color: var(--white); letter-spacing: 1px;
  }
  .product-title sup { font-size: 30px; vertical-align: 30px; margin-left: 4px; }

  /* Footer bands */
  .edition-band {
    position: absolute; left: 0; top: 614px; width: 380px; height: 58px;
    background: var(--green);
  }
  .edition-band .notch { position: absolute; left: 0; top: 0; }
  .edition-band .edition-title {
    position: absolute; left: 58px; top: 5px;
    font-family: "Bree Serif", Georgia, serif; font-size: 27px; color: var(--white);
  }
  .edition-band .edition-org {
    position: absolute; left: 58px; top: 38px;
    font-size: 12px; font-weight: 500; color: var(--ink); text-transform: uppercase; letter-spacing: .3px;
  }
  .contact-band {
    position: absolute; right: 0; top: 692px; width: 230px; height: 84px;
    background: var(--green); padding: 10px 16px 0 0; text-align: right; color: var(--white);
  }
  .contact-band .contact-url { font-size: 16px; font-weight: 700; }
  .contact-band p { font-size: 11px; line-height: 13px; margin-top: 4px; }
</style>
</head>
<body>
  <article class="cover">
    <header class="cover-header">
      <h1 class="org-name">Office of Digital<br>Reachworks</h1>
      <div class="org-mark">
        <span class="disc"></span>
        <span class="mark-name">ODR.org</span>
      </div>
      <blockquote class="mission-quote">
        <div class="quote-mark">“</div>
        <span class="quote-rule"></span>
        <p>The mission of the ODR team is to make the Internet accessible for everyone.</p>
        <span class="quote-rule"></span>
        <div class="quote-url">www.qelvantrix.org</div>
        <div class="quote-mark close">”</div>
      </blockquote>
    </header>

    <div class="cover-photo" role="img" aria-label="Photo of a person's hands interacting with a floating grid of translucent digital app icons on a dark blue background"></div>

    <h2 class="product-title">FlintVue<sup>™</sup></h2>

    <div class="edition-band">
      <svg class="notch" width="48" height="58" viewBox="0 0 48 58" aria-hidden="true">
        <polygon points="0,0 48,0 0,58" fill="#ffffff"/>
      </svg>
      <div class="edition-title">2019 Brochure</div>
      <div class="edition-org">Office of Digital Reachworks</div>
    </div>

    <footer class="contact-band">
      <div class="contact-url">www.qelvantrix.org</div>
      <p>The mission of the ODR team is to make the Internet accessible for everyone.</p>
    </footer>
  </article>
</body>
</html>
```